New Alcoholic Spiked Seltzer Line

We need a can design for a line of low calorie alcoholic seltzer. This product is a sparkling water and vodka drink with no sugar added in a slim 12 oz can.

This is a lighter, healthier, alternative to the sugary ready-to-drinks on the market. The product contains only 3 ingredients: Vodka, Water and Natural Flavors. It has only 100 calories but still has 5% alcohol, so you don't need to sacrifice alcohol to cut calories.

This product also does not contain any preservatives.

We want this design to communicate the following objectives to the consumer and in this order:

1. Appetizing product
2.Low calorie
3.Communicate the type of beverage (Spiked Seltzer)

The brand name of the product is VELKA.

The flavor of the product needed to be used for the design is Mango-Orange.

Comparable products are:

www.brindlefizzworks.example/
https://www.quorvabubbles.example
https://pelnavo.example/

The designs should not infringe or copy the creative directions of the products mentionned above. They are only given so that you can better understand the type of product we are developing.

Target Market(s)

Young Professional women between the ages of 25 and 44

Industry/Entity Type

Product

Colors

Designer to choose colors to be used in the design.

Requirements
Must have
• Design extendibility, meaning it can be adapted for other flavors.
• This is a new category in the market we are targeting, so consumers must easily be able to identify what type of product this is.

```html
<!DOCTYPE html>
<html lang="en">
<head>
<meta charset="utf-8">
<title>VELKA Spiked Seltzer – Mango Orange Can Label</title>
<link rel="stylesheet" href="https://fonts.googleapis.com/css2?family=Montserrat:wght@500;600;700&display=swap">
<style>
  :root {
    --backdrop: #eef1f4;
    --label-white: #ffffff;
    --mango-yellow: #f3c21f;
    --mango-deep: #e3ad12;
    --ink: #1c1c1c;
    --shadow: rgba(20, 30, 45, 0.14);
  }
  html, body {
    margin: 0;
    width: 1197px;
    height: 1200px;
    overflow: hidden;
    background: var(--backdrop);
  }
  .canvas {
    position: relative;
    width: 1197px;
    height: 1200px;
  }
  .can-label {
    position: absolute;
    left: 388px;
    top: 60px;
    width: 420px;
    height: 1080px;
    border-radius: 18px;
    overflow: hidden;
    box-shadow: 0 18px 40px var(--shadow);
    background: var(--label-white);
  }
  .can-label svg { display: block; }
  .brand-name {
    font-family: "Montserrat", sans-serif;
    font-weight: 600;
    fill: var(--ink);
  }
  .category {
    font-family: "Montserrat", sans-serif;
    font-weight: 600;
    fill: var(--ink);
  }
  .flavor {
    font-family: "Montserrat", sans-serif;
    font-weight: 600;
    fill: var(--mango-deep);
  }
  .claim {
    font-family: "Montserrat", sans-serif;
    font-weight: 500;
    fill: var(--ink);
  }
  .yellow-fill { fill: var(--mango-yellow); }
</style>
</head>
<body>
  <main class="canvas">
    <section class="can-label" aria-label="VELKA Spiked Seltzer Mango Orange can label">
      <svg width="420" height="1080" viewBox="0 0 420 1080" xmlns="http://www.w3.org/2000/svg">
        <polygon class="yellow-fill diagonal-block" points="0,0 420,0 420,20 0,630"/>

        <text class="brand-name" x="0" y="0" font-size="128" textLength="540" lengthAdjust="spacingAndGlyphs"
              transform="translate(88 712) rotate(-54)">VELKA</text>

        <text class="category" x="0" y="0" font-size="38" textLength="400" lengthAdjust="spacingAndGlyphs"
              transform="translate(150 728) rotate(-54)">SPIKED SELTZER</text>

        <text class="flavor" x="272" y="716" font-size="30">MANGO</text>
        <text class="flavor" x="272" y="762" font-size="30">ORANGE</text>

        <text class="claim" x="210" y="920" font-size="17" text-anchor="middle">Appetizing product</text>

        <rect class="yellow-fill info-band" x="0" y="932" width="420" height="42"/>
        <text class="claim" x="210" y="959" font-size="17" text-anchor="middle">100 cal  /  5%alc.</text>
      </svg>
    </section>
  </main>
</body>
</html>
```